Financial Advisor Resource Firm needs business card design

Need business card design for company in Omaha NE called Meridale Circle. We provide resources to financial advisors....workshop programs, retirement analysis, and insurance planning. I would like to see designs that use grays, greens, black, and white colors. The final design should communicate 'collaboration' and be simple yet attractive to financial planning clients. I will attached our logo and another picture of a puzzle piece coming together. I would like the incorporate the puzzle picture somehow, maybe on the back somehow, with color or just the gray scale....OR, the picture be the front of the card with 'Meridale' definition on it (see upload) and then company logo, employee name, title, address on the back (see ppt uploaded). The following disclosure needs to be included somewhere- Advisory services offered through Stonebrook Assets, LLC.
Updates

I uploaded a svg and ai file of the logo

Target Market(s)

Financial planning clients and financial advisors....so pretty diverse age range of about 40-70.

Industry/Entity Type

Financial Planning

Contact Information for Business Card

Tobias L. Fenwright, MBA
Founder/President
5287 E. Larkin Road
Suite 230
Omaha, NE 68190
Phone- (402) 555-0147
Cell- (402) 555-0183
Fax- (402) 555-0129
email- tobias@meridaleplan.example
web address- www.meridaleplan.example

Colors
1b1b1b
474747
d3d3d3
ffffff
9bcb3c
abd036

Requirements
Must have
• Must include logo provided, must be 2 sided, and must have disclosure...all of these items listed in project description

```html
<!DOCTYPE html>
<html lang="en">
<head>
<meta charset="utf-8">
<title>Meridale Circle — Business Card</title>
<link rel="stylesheet" href="https://fonts.googleapis.com/css2?family=Montserrat:wght@400;500&display=swap">
<style>
  :root {
    --page: #f4f4f4;
    --ink: #1b1b1b;
    --slate: #474747;
    --mist: #d3d3d3;
    --white: #ffffff;
    --green: #9bcb3c;
    --green-bright: #abd036;
  }
  html, body {
    margin: 0;
    width: 1200px;
    height: 900px;
    overflow: hidden;
    background: var(--page);
    font-family: "Montserrat", Arial, sans-serif;
  }
  .canvas { position: relative; width: 1200px; height: 900px; }
  .card {
    position: absolute;
    top: 141px;
    width: 354px;
    height: 619px;
    background: var(--ink);
    overflow: hidden;
    box-shadow: 0 18px 30px rgba(0,0,0,0.18);
  }
  .card--front { left: 209px; }
  .card--back { left: 637px; }
  .card__art { position: absolute; inset: 0; }
  .wordmark {
    position: absolute;
    left: 0; right: 0;
    margin: 0;
    text-align: center;
    color: var(--white);
    font-weight: 500;
    letter-spacing: 0.06em;
    line-height: 1.05;
    text-transform: uppercase;
  }
  .card--front .wordmark { top: 420px; font-size: 31px; }
  .wordmark__sub { display: block; font-size: 0.45em; letter-spacing: 0.22em; margin-top: 4px; }
  .tagline {
    position: absolute;
    top: 490px; left: 0; right: 0;
    margin: 0;
    text-align: center;
    color: var(--white);
    font-size: 14.5px;
    line-height: 19px;
  }
  .accent { color: var(--green); }
  .disclosure {
    position: absolute;
    left: 0; right: 0; bottom: 16px;
    margin: 0;
    text-align: center;
    color: var(--mist);
    font-size: 9px;
    letter-spacing: 0.03em;
    opacity: 0.75;
  }
  .card--back .wordmark { top: 121px; font-size: 21px; }
  .contact {
    position: absolute;
    top: 296px; left: 0; right: 0;
    text-align: center;
    color: var(--white);
  }
  .contact__name { font-size: 21px; color: var(--green); margin: 0; letter-spacing: 0.01em; }
  .contact__cred { color: var(--white); font-size: 15px; }
  .contact__title { font-size: 15px; margin: 2px 0 0; }
  .contact__icons { margin: 14px 0 6px; height: 20px; }
  .contact__lines { font-size: 15.5px; line-height: 24.3px; margin: 0; letter-spacing: 0.02em; }
  .address {
    position: absolute;
    left: 0; right: 0; top: 560px;
    text-align: center;
    color: var(--white);
    font-style: normal;
    font-size: 15px;
    line-height: 20px;
    letter-spacing: 0.02em;
  }
</style>
</head>
<body>
<main class="canvas">

  <section class="card card--front">
    <svg class="card__art" width="354" height="619" viewBox="0 0 354 619">
      <defs>
        <linearGradient id="frontPhoto" x1="0" y1="0" x2="1" y2="1">
          <stop offset="0" stop-color="#d9d9d9"/>
          <stop offset="0.45" stop-color="#8e8e8e"/>
          <stop offset="1" stop-color="#3a3a3a"/>
        </linearGradient>
      </defs>
      <path role="img" aria-label="Grayscale photo of hands joining puzzle pieces"
            d="M0,0 H354 V250 H311 A143,143 0 0,1 43,250 H0 Z" fill="url(#frontPhoto)"/>
      <path d="M332,250 H311 A143,143 0 0,1 43,250 H22" fill="none" stroke="var(--green)" stroke-width="3" stroke-linecap="round"/>
    </svg>
    <p class="wordmark">Meridale<span class="wordmark__sub">Circle</span></p>
    <p class="tagline">To come <span class="accent">TOGETHER</span> and <span class="accent">UNITE</span><br>in common interest<br>and <span class="accent">FOCUS</span></p>
    <p class="disclosure">Advisory services offered through Stonebrook Assets, LLC</p>
  </section>

  <section class="card card--back">
    <svg class="card__art" width="354" height="619" viewBox="0 0 354 619">
      <defs>
        <linearGradient id="backPhoto" x1="0" y1="0" x2="1" y2="1">
          <stop offset="0" stop-color="#cfcfcf"/>
          <stop offset="0.5" stop-color="#8a8a8a"/>
          <stop offset="1" stop-color="#3d3d3d"/>
        </linearGradient>
      </defs>
      <path role="img" aria-label="Grayscale photo of hands joining puzzle pieces"
            d="M0,0 H354 V183 H308 A143,143 0 0,1 44,183 H0 Z" fill="url(#backPhoto)"/>
      <circle cx="176" cy="129" r="113" fill="var(--green)" opacity="0.55"/>
      <circle cx="176" cy="129" r="104" fill="var(--green-bright)" opacity="0.35"/>
      <path d="M332,183 H308 A143,143 0 0,1 44,183 H22" fill="none" stroke="var(--green)" stroke-width="3" stroke-linecap="round"/>
      <rect class="address-band" x="0" y="546" width="354" height="73" fill="var(--green)"/>
      <circle cx="177" cy="540" r="29" fill="var(--green)"/>
      <path class="pin" d="M177,532 a7,7 0 0,1 7,7 c0,5 -7,12 -7,12 c0,0 -7,-7 -7,-12 a7,7 0 0,1 7,-7 z M177,536 a3,3 0 1,0 0.01,0 z"
            fill="var(--white)" fill-rule="evenodd"/>
    </svg>
    <p class="wordmark">Meridale<span class="wordmark__sub">Circle</span></p>

    <div class="contact">
      <p class="contact__name">Tobias L. Fenwright<span class="contact__cred">, MBA</span></p>
      <p class="contact__title">Founder | President</p>
      <svg class="contact__icons" width="130" height="20" viewBox="0 0 130 20" fill="var(--green)">
        <path d="M3,3 l4,-1 l2,5 l-2,2 a10,10 0 0,0 5,5 l2,-2 l5,2 l-1,4 c-9,1 -16,-6 -15,-15 z"/>
        <rect x="30" y="1" width="10" height="18" rx="2"/><rect x="32" y="3" width="6" height="11" fill="var(--ink)"/>
        <rect x="52" y="4" width="5" height="15" rx="1"/><rect x="58" y="2" width="10" height="17" rx="1"/>
        <rect x="60" y="5" width="6" height="2" fill="var(--ink)"/><rect x="60" y="9" width="6" height="2" fill="var(--ink)"/>
        <rect x="78" y="4" width="17" height="12" rx="1"/><path d="M78,5 l8.5,6 l8.5,-6" stroke="var(--ink)" stroke-width="1.5" fill="none"/>
        <circle cx="113" cy="10" r="8.5"/><path d="M107,7 q3,-2 5,1 q-1,3 -3,3 z M114,12 q3,0 4,3 q-3,2 -5,0 z" fill="var(--ink)"/>
      </svg>
      <p class="contact__lines">
        (402) 555 - 0147<br>
        (402) 555 - 0183<br>
        (402) 555 - 0129<br>
        tobias@meridaleplan.example<br>
        www.<span class="accent">meridaleplan</span>.example
      </p>
    </div>

    <address class="address">5287 E. Larkin Road<br>Suite 230, Omaha, NE 68190</address>
  </section>

</main>
</body>
</html>
```